Brightway Haus Inc. Business Card Design

Brightway Haus Inc. is in search of a great clean design for our business cards!

Looking to incorporate our full logo and watermark on side one (however, I am open to having the text and watermark separated within the design.)

On side two, I am looking to have contact information (Name, Position, Phone #, Email, Website (www.thebrightwayhaus.ca). Can have the logo and/or watermark as part of the design if applicable.

Please add tagline "Where Shine Counts" on either side 1 or 2. This tagline can be in a sans serif, serif or cursive font as long as it compliments overall design. Capitalization can be title or sentence case depending on how it fits within the design.

Get creative!! Looking for a clean, crisp, premium design! Looking for a glossy card finish with spot UV features when printed. Cards will also be printed with rounded corners. Standard dimensions (3.5 x 2).

Target Market(s)

B2B - primary clients are business owners or property management corporations. (residential jobs are few and far between)

Industry/Entity Type

Business

Contact Information for Business Card

- clean, crisp design
- double sided
- spot UV accents and glossy finish upon printing
- standard business card size (3.5 x 2) with rounded corners
- please see project description for requirements per side

Font styles to use
Sans Serif

Requirements
Must have
• - adequate bleeds with print ready files
• - cohesive design elements between side 1 & 2
• - spot UV elements (can be on both sides or just one, use your discretion)
• - colour pallet should match the logo file provided
• - incorporate tagline "where shine counts" (this tagline can be in a serif or sans serif font as long as it is complimentary to the overall design.
Nice to have
• - Premium elements with a clean design
Should not have
• - Please omit cartoon or whimsical like designs, think premium.
• - Colours should not stray from the pallet of the provided logo.

```html
<!DOCTYPE html>
<html lang="en">
<head>
<meta charset="utf-8">
<title>Brightway Haus Inc. Business Card</title>
<link href="https://fonts.googleapis.com/css2?family=Roboto:wght@400;500;700&display=swap" rel="stylesheet">
<style>
  :root {
    --backdrop: #e4e4e4;
    --card: #efefef;
    --card-edge: #e2e2e2;
    --teal: #159e9b;
    --navy: #1f1d45;
    --grey: #9a9a9a;
    --mark-tint: rgba(200, 200, 200, 0.45);
  }
  * { box-sizing: border-box; margin: 0; padding: 0; }
  html, body { width: 1200px; height: 576px; overflow: hidden; }
  body {
    background: var(--backdrop);
    font-family: "Roboto", Arial, sans-serif;
    position: relative;
  }
  .card {
    position: absolute;
    top: 139px;
    width: 484px;
    height: 293px;
    border-radius: 14px;
    background: linear-gradient(160deg, #f4f4f4 0%, var(--card) 55%, var(--card-edge) 100%);
    overflow: hidden;
  }
  .card--front { left: 82px; }
  .card--back { left: 602px; }

  .spot-mark {
    position: absolute;
    border-radius: 50% 50% 46% 46% / 60% 60% 40% 40%;
    background: radial-gradient(ellipse at 50% 60%, var(--mark-tint) 0%, rgba(210,210,210,0.15) 70%, transparent 100%);
  }
  .card--front .spot-mark { left: 230px; top: 10px; width: 230px; height: 270px; }
  .card--back .spot-mark { left: 240px; top: 20px; width: 230px; height: 270px; }

  .brand {
    position: absolute;
    display: flex;
    align-items: center;
    gap: 10px;
  }
  .brand__square {
    width: 30px; height: 30px;
    background: var(--teal);
  }
  .brand__name {
    font-weight: 700;
    color: var(--teal);
    letter-spacing: -0.5px;
    white-space: nowrap;
  }
  .card--front .brand { left: 58px; top: 128px; }
  .card--front .brand__name { font-size: 32px; }

  .edge-tab {
    position: absolute;
    left: -18px; top: 33px;
    width: 28px; height: 56px;
    border-radius: 50%;
    background: var(--teal);
  }
  .person { position: absolute; left: 25px; top: 40px; }
  .person__name { font-size: 21px; font-weight: 700; color: var(--teal); }
  .person__role { font-size: 11.5px; color: var(--navy); margin-top: 4px; }

  .corner-square {
    position: absolute;
    left: 372px; top: 30px;
    width: 58px; height: 58px;
    background: var(--teal);
  }

  .address {
    position: absolute; left: 25px; top: 178px;
    font-size: 12.5px; line-height: 17px; color: var(--navy);
  }
  .contacts {
    position: absolute; left: 25px; top: 219px;
    list-style: none;
    font-size: 12.5px; color: var(--navy);
  }
  .contacts li { display: flex; align-items: center; gap: 10px; height: 18px; }
  .contacts svg { width: 10px; height: 10px; fill: var(--teal); }
  .contacts .accent { color: var(--teal); }

  .signature {
    position: absolute; right: 25px; top: 224px;
    text-align: right;
  }
  .signature__name { font-size: 21px; font-weight: 700; color: var(--teal); letter-spacing: -0.3px; }
  .signature__tagline {
    font-size: 10.5px; color: var(--navy);
    letter-spacing: 3px; margin-top: 4px;
  }
</style>
</head>
<body>
  <section class="card card--front">
    <div class="spot-mark" role="img" aria-label="Faint spot UV brand watermark"></div>
    <div class="brand">
      <span class="brand__square"></span>
      <span class="brand__name">BRIGHTWAY HAUS INC.</span>
    </div>
  </section>

  <section class="card card--back">
    <div class="spot-mark" role="img" aria-label="Faint spot UV brand watermark"></div>
    <span class="edge-tab"></span>
    <div class="person">
      <p class="person__name">Mara Ellison</p>
      <p class="person__role">Managing Director</p>
    </div>
    <span class="corner-square"></span>

    <p class="address">48 Harbour Lane, Suite 2,<br>Canada</p>
    <ul class="contacts">
      <li>
        <svg viewBox="0 0 10 10"><path d="M2 0.5 L3.6 2.8 L2.6 3.8 Q4 6.2 6.2 7.4 L7.2 6.4 L9.5 8 L8.2 9.6 Q3.5 9 0.5 1.8 Z"/></svg>
        <span>1800-555-0142</span>
      </li>
      <li>
        <svg viewBox="0 0 10 10"><path d="M0 1.5 H10 V8.5 H0 Z M0.8 2.3 L5 5.4 L9.2 2.3 Z" fill-rule="evenodd"/></svg>
        <span>mara@brightwayhaus.ca</span>
      </li>
      <li>
        <svg viewBox="0 0 10 10"><circle cx="5" cy="5" r="4.6"/><path d="M0.5 5 H9.5 M5 0.4 V9.6" stroke="#efefef" stroke-width="0.8"/></svg>
        <span>www.<span class="accent">thebrightwayhaus</span>.ca</span>
      </li>
    </ul>

    <div class="signature">
      <p class="signature__name">BRIGHTWAY HAUS INC.</p>
      <p class="signature__tagline">Where Shine Counts</p>
    </div>
  </section>
</body>
</html>
```